New Graphic Design Project / Email signiture and Letterhead

I would like a new SIMPLE but high end quality modern/heavy industrial design for an email Signiture and letter head that incorporates product photos or illustrations of our products to show our customers our range of products and also show our head office in Perth Western Australia and also our Australian and international reseller locations.
in my present email signature you would see that I have other company logos these companies are old partners of ours but some are no longer so I would like to have the option to add and change them if things change in the future.
for ideas Our main products are as follows
Composite Hose
Convoluted hose
Metal expansion joints
Fabric expansion joints
Rubber Expansion joints
Please see our website for ideas and our product photos.
www.norvaquip.com.au
if you need any further information please let me know
i have attached our old email signiture for reference.
Dale

Target Market(s)

Oil and Gas / Mining / Petroleum and Chemical Refineries, high end engineering

Requirements
Must have
• pictures / photos of our core products and our company capabilities to show our existing and new customers what we can do.
in the email signature - links to company face book and LinkedIn, our website
I would like to have spaces for my company partners logos and need the final file to be in a format for me to change and update all details
All so our Font is Conthrax SB
Nice to have
• the email signature, I would like this to have all the required information ( as per attached present email signature ) but also be informative / marketing to show customers what we do if possible.
the letter head can be based from the same but simple with or without product photos

```html
<!DOCTYPE html>
<html lang="en">
<head>
<meta charset="utf-8">
<title>Norvaquip – Letterhead and Email Signature</title>
<link href="https://fonts.googleapis.com/css2?family=Roboto:wght@400;500;700&display=swap" rel="stylesheet">
<style>
  :root{
    --brand-blue:#1f78c8;
    --ink:#2b2b2b;
    --ink-soft:#6a6a6a;
    --rule:#d4d4d4;
    --page:#ffffff;
    --canvas:#ffffff;
    --badge:#e3e6ea;
    --social-a:#3b5998;
    --social-b:#4aa84c;
    --social-c:#d9534f;
    --social-d:#0e76a8;
  }
  *{box-sizing:border-box;margin:0;padding:0}
  html,body{width:747px;height:1200px;overflow:hidden;background:var(--canvas)}
  body{position:relative;font-family:"Roboto",Arial,sans-serif;color:var(--ink)}

  .wordmark{display:flex;align-items:center;gap:8px}
  .wordmark__dot{width:22px;height:22px;border-radius:50%;background:var(--ink)}
  .wordmark__name{font-weight:700;color:var(--ink);letter-spacing:1px}

  /* Letterhead */
  .letterhead{position:absolute;left:62px;top:14px;width:628px;height:834px;background:var(--page);
    box-shadow:0 3px 14px rgba(0,0,0,.18)}
  .letterhead__header{position:absolute;left:36px;top:70px}
  .letterhead__header .wordmark__name{font-size:26px}
  .letterhead__rule{position:absolute;left:0;right:0;height:4px;background:var(--brand-blue)}
  .letterhead__rule--top{top:108px}
  .letterhead__rule--bottom{bottom:14px}
  .letterhead__contact{position:absolute;right:26px;top:150px;height:610px;writing-mode:vertical-rl;
    transform:rotate(180deg);display:flex;gap:26px;font-size:10.5px;color:var(--ink-soft);align-items:center}
  .letterhead__contact span{display:flex;align-items:center;gap:5px}
  .letterhead__contact svg{transform:rotate(90deg)}
  .letterhead__signoff{position:absolute;left:36px;bottom:58px;font-size:10.5px;line-height:1.35;color:var(--ink-soft)}
  .letterhead__signoff strong{color:var(--ink);font-weight:700}

  /* Email signature */
  .signature{position:absolute;left:62px;top:908px;width:628px;height:262px;background:var(--page);
    box-shadow:0 3px 14px rgba(0,0,0,.18)}
  .signature__brand{position:absolute;left:22px;top:28px;width:210px}
  .signature__brand .wordmark__name{font-size:24px}
  .signature__products{margin-top:16px;height:46px;border-radius:4px;
    background:linear-gradient(90deg,#9aa3ab,#c7ccd1,#8e969d)}
  .signature__divider{position:absolute;left:248px;top:26px;width:2px;height:140px;background:var(--ink)}
  .signature__person{position:absolute;left:270px;top:30px;width:340px}
  .signature__name{font-size:25px;font-weight:700;color:var(--ink)}
  .signature__role{font-size:13px;color:var(--ink-soft);margin-top:2px}
  .signature__social{position:absolute;right:0;top:8px;display:flex;gap:6px}
  .signature__social span{width:14px;height:14px;border-radius:2px}
  .contact-grid{display:grid;grid-template-columns:1fr 1fr;gap:5px 12px;margin-top:18px;font-size:11px;color:var(--ink)}
  .contact-grid span{display:flex;align-items:center;gap:7px}
  .locations{display:flex;gap:10px;margin-top:12px;font-size:11px;color:var(--ink)}
  .locations i{font-style:normal;color:var(--rule)}
  .signature__partners{position:absolute;left:22px;right:22px;top:186px;display:flex;justify-content:space-between;
    padding-top:10px;border-top:1px solid var(--rule)}
  .partner-badge{width:56px;height:34px;background:var(--badge);border-radius:3px}
  .signature__rule{position:absolute;left:0;right:0;bottom:12px;height:4px;background:var(--brand-blue)}
</style>
</head>
<body>

<section class="letterhead">
  <div class="letterhead__header wordmark">
    <span class="wordmark__dot"></span><span class="wordmark__name">NORVAQUIP</span>
  </div>
  <div class="letterhead__rule letterhead__rule--top"></div>

  <div class="letterhead__contact">
    <span><svg width="9" height="11" viewBox="0 0 10 12"><path d="M5 0a4 4 0 0 0-4 4c0 3 4 8 4 8s4-5 4-8a4 4 0 0 0-4-4z" fill="#1f78c8"/></svg>12 Kestrel Road Forrestdale WA 6112</span>
    <span><svg width="10" height="10" viewBox="0 0 10 10"><path d="M2 0l2 2-1 2 3 3 2-1 2 2-2 2C4 10 0 6 0 2z" fill="#1f78c8"/></svg>+614 5520 3184 · +618 9390 4427</span>
    <span><svg width="10" height="10" viewBox="0 0 10 10"><circle cx="5" cy="5" r="4.5" fill="#1f78c8"/></svg>www.norvaquip.com.au</span>
  </div>

  <div class="letterhead__signoff">
    <strong>Dale Marsh</strong><br>Managing Director<br>dale@norvaquip.com.au
  </div>
  <div class="letterhead__rule letterhead__rule--bottom"></div>
</section>

<section class="signature">
  <div class="signature__brand">
    <div class="wordmark"><span class="wordmark__dot"></span><span class="wordmark__name">NORVAQUIP</span></div>
    <div class="signature__products" role="img" aria-label="Product photos: composite hose, convoluted hose and expansion joints"></div>
  </div>
  <div class="signature__divider"></div>

  <div class="signature__person">
    <div class="signature__name">Dale Marsh</div>
    <div class="signature__role">Managing Director</div>
    <div class="signature__social">
      <span style="background:var(--social-a)"></span><span style="background:var(--social-b)"></span>
      <span style="background:var(--social-c)"></span><span style="background:var(--social-d)"></span>
    </div>
    <div class="contact-grid">
      <span><svg width="10" height="10" viewBox="0 0 10 10"><path d="M2 0l2 2-1 2 3 3 2-1 2 2-2 2C4 10 0 6 0 2z" fill="#2b2b2b"/></svg>+614 5520 3184</span>
      <span><svg width="10" height="10" viewBox="0 0 10 10"><circle cx="5" cy="5" r="4.5" fill="#2b2b2b"/></svg>www.norvaquip.com.au</span>
      <span><svg width="10" height="10" viewBox="0 0 10 10"><rect x="1" y="0" width="8" height="10" rx="1" fill="#2b2b2b"/></svg>+618 9390 4427</span>
      <span><svg width="9" height="11" viewBox="0 0 10 12"><path d="M5 0a4 4 0 0 0-4 4c0 3 4 8 4 8s4-5 4-8a4 4 0 0 0-4-4z" fill="#2b2b2b"/></svg>12 Kestrel Road</span>
      <span><svg width="10" height="8" viewBox="0 0 10 8"><rect width="10" height="8" rx="1" fill="#2b2b2b"/></svg>dale@norvaquip.com.au</span>
      <span style="padding-left:16px">Forrestdale, WA 6112</span>
    </div>
    <div class="locations">
      <span>Australia</span><i>|</i><span>Singapore</span><i>|</i><span>Indonesia</span><i>|</i><span>Vietnam</span>
    </div>
  </div>

  <div class="signature__partners">
    <span class="partner-badge"></span><span class="partner-badge"></span><span class="partner-badge"></span>
    <span class="partner-badge"></span><span class="partner-badge"></span><span class="partner-badge"></span>
    <span class="partner-badge"></span><span class="partner-badge"></span><span class="partner-badge"></span>
  </div>
  <div class="signature__rule"></div>
</section>

</body>
</html>
```